RWT Fittings Ltd Business Cards

We need a business card with our business logo. We provide window and door installations on high-rises in west coast British Colombia, Canada.

I would like my business information and details on one side of the card, and the other side the company name with logo

Target Market(s)

General Contractors

Industry/Entity Type

Construction

Contact Information for Business Card

one side i want my company name and logo in the dark theme logo that i provided

Requirements
Must have
• Marco Peltieri, 16045518293, RWTFittings@mailbox-demo.com, 1407-5194 Linden Row Burnaby BC, V5H 2K9, Owner & Manager

```html
<!DOCTYPE html>
<html lang="en">
<head>
<meta charset="utf-8">
<title>RWT Fittings Ltd – Business Cards</title>
<link rel="stylesheet" href="https://fonts.googleapis.com/css2?family=Montserrat:wght@400;500;700&display=swap">
<style>
  :root {
    --page-bg: #4a4a4a;
    --card-white: #ffffff;
    --brand-blue: #27a7e0;
    --brand-grey: #9a9a9a;
    --ink: #2b2b2b;
    --card-black: #161616;
    --card-black-edge: #242424;
  }
  * { margin: 0; padding: 0; box-sizing: border-box; }
  html, body {
    width: 1200px; height: 780px; overflow: hidden;
    background: var(--page-bg);
    font-family: "Montserrat", sans-serif;
  }
  .sheet {
    width: 1200px; height: 780px;
    display: flex; align-items: center; justify-content: center; gap: 40px;
  }
  .card {
    position: relative;
    width: 540px; height: 309px;
    overflow: hidden;
    box-shadow: 0 14px 30px rgba(0,0,0,.45);
  }

  /* Front */
  .card-front { background: var(--card-white); }
  .front-swoosh { position: absolute; inset: 0; }
  .front-brand {
    position: absolute; left: 40px; top: 30px;
    display: flex; align-items: center; gap: 10px;
    color: var(--brand-blue); font-weight: 700; font-size: 26px; letter-spacing: .5px;
  }
  .brand-mark { width: 22px; height: 22px; background: var(--brand-blue); }
  .contact {
    position: absolute; left: 40px; top: 84px;
    color: var(--ink); font-size: 12.5px; line-height: 1.5;
  }
  .contact-address { margin-bottom: 7px; }
  .contact-line { display: flex; align-items: center; gap: 7px; }
  .contact-icon { width: 11px; height: 11px; flex: none; }
  .person {
    position: absolute; right: 34px; top: 108px; text-align: right;
  }
  .person-name {
    color: var(--brand-blue); font-weight: 700; font-size: 20px; letter-spacing: .5px;
  }
  .person-role { color: var(--ink); font-size: 14px; margin-top: 2px; }

  /* Back */
  .card-back {
    background: radial-gradient(ellipse at 50% 45%, var(--card-black-edge), var(--card-black) 75%);
    display: flex; align-items: center; justify-content: center;
  }
  .back-brand {
    display: flex; align-items: center; gap: 12px;
    color: var(--brand-blue); font-weight: 700; font-size: 30px; letter-spacing: .5px;
  }
  .back-brand .brand-mark { width: 26px; height: 26px; }
</style>
</head>
<body>
<main class="sheet">

  <section class="card card-front" aria-label="Business card front">
    <svg class="front-swoosh" viewBox="0 0 540 309" width="540" height="309" aria-hidden="true">
      <path d="M0 212 C 45 268, 140 292, 260 294 L 540 272 L 540 309 L 0 309 Z" fill="var(--brand-blue)"/>
      <path d="M14 208 C 58 258, 140 282, 250 286" fill="none" stroke="var(--brand-grey)" stroke-width="6"/>
      <rect x="526" y="168" width="14" height="141" fill="var(--brand-blue)"/>
    </svg>

    <div class="front-brand"><span class="brand-mark"></span>RWT Fittings Ltd</div>

    <div class="contact">
      <p class="contact-address">1407-5194 Linden Row<br>Burnaby BC, V5H 2K9</p>
      <p class="contact-line">
        <svg class="contact-icon" viewBox="0 0 12 12" aria-hidden="true"><path d="M2 1h3l1 3-2 1a7 7 0 0 0 3 3l1-2 3 1v3a1 1 0 0 1-1 1A10 10 0 0 1 1 2a1 1 0 0 1 1-1z" fill="var(--brand-blue)"/></svg>
        16045518293
      </p>
      <p class="contact-line">
        <svg class="contact-icon" viewBox="0 0 12 12" aria-hidden="true"><rect x="1" y="2.5" width="10" height="7" rx="1" fill="var(--brand-blue)"/><path d="M1.5 3l4.5 3.5L10.5 3" fill="none" stroke="#fff" stroke-width="1"/></svg>
        RWTFittings@mailbox-demo.com
      </p>
      <p class="contact-line">
        <svg class="contact-icon" viewBox="0 0 12 12" aria-hidden="true"><circle cx="6" cy="6" r="5" fill="var(--brand-blue)"/><path d="M1 6h10M6 1c-2 3-2 7 0 10M6 1c2 3 2 7 0 10" fill="none" stroke="#fff" stroke-width=".8"/></svg>
        www.rwtfittings-demo.com
      </p>
    </div>

    <div class="person">
      <p class="person-name">MARCO PELTIERI</p>
      <p class="person-role">Owner &amp; Manager</p>
    </div>
  </section>

  <section class="card card-back" aria-label="Business card back">
    <div class="back-brand"><span class="brand-mark"></span>RWT Fittings Ltd</div>
  </section>

</main>
</body>
</html>
```